OrvanoGoodsHub.com -Ecommerce Website for Luxury Products

This will be an ecommerce site. A website portal that will allow both consumers to enter one way and see specific purchase options and businesses to enter via a different link that allows B2B to see their specific options once logged into. B2C can purchase both as a guest/or after account is setup. B2B must be approved to set up account. This is front end website project. Back-end integration is separate. Will be hosted on Servantia with a domain registration held at Pexadrinet. Additional website concept/idea/synergy can be found from sister site-KRWZHospitality.com

```html
<!DOCTYPE html>
<html lang="en">
<head>
<meta charset="utf-8">
<title>OrvanoGoods — Purveyors of Luxury Lifestyle Accoutrements</title>
<link href="https://fonts.googleapis.com/css2?family=Gilda+Display&family=DM+Sans:wght@400;500;600&display=swap" rel="stylesheet">
<style>
:root{
  --bg:#0c0c0c;
  --bg-soft:#141414;
  --panel:#161616;
  --gold:#9b7e4e;
  --gold-text:#ab8b58;
  --gold-line:#6e5a39;
  --white:#f3efe8;
  --muted:#cfc8bd;
  --black:#0a0a0a;
  --serif:"Gilda Display", "Times New Roman", serif;
  --sans:"DM Sans", Arial, sans-serif;
}
*{margin:0;padding:0;box-sizing:border-box}
html,body{width:1200px;height:4781px;overflow:hidden;background:var(--bg)}
body{font-family:var(--sans);color:var(--white)}
.page{position:relative;width:1200px;height:4781px;overflow:hidden;background:var(--bg)}
.abs{position:absolute}
.btn{position:absolute;display:flex;align-items:center;justify-content:center;font-family:var(--sans);font-size:13px;font-weight:500;color:var(--white);text-decoration:none}
.btn--gold{background:var(--gold)}
.btn--outline{border:1.5px solid var(--gold);color:var(--gold-text)}
.btn--dark{background:var(--black)}
.mark{position:absolute;width:22px;height:2px;background:var(--white);left:50%;transform:translateX(-50%)}
.mark--left{left:0;transform:none}
.title{font-family:var(--serif);font-weight:400;font-size:37px;letter-spacing:.5px;text-transform:uppercase;color:var(--white);line-height:1.1}
.title em{font-style:normal;color:var(--gold-text)}
.center{text-align:center;left:0;width:1200px}
.copy{font-size:13.5px;line-height:25px;color:var(--muted)}

/* Brand wordmark */
.brand{position:absolute;text-align:center;font-family:var(--serif);color:var(--white)}
.brand__monogram{width:22px;height:22px;border-radius:50%;border:1.5px solid var(--white);margin:0 auto 6px}
.brand__name{font-size:20px;letter-spacing:1px;line-height:1}
.brand__sub{font-family:var(--sans);font-size:6.5px;letter-spacing:1.5px;margin-top:4px;text-transform:uppercase}
.brand__tag{font-size:8.5px;margin-top:5px;color:var(--muted)}

/* Hero */
.hero{position:absolute;left:0;top:0;width:1200px;height:815px}
.hero__media{position:absolute;inset:0;background:radial-gradient(ellipse at 75% 45%,#4a3520 0%,#261a10 30%,#141110 60%,#0d0c0b 100%)}
.hero__shade{position:absolute;inset:0;background:linear-gradient(90deg,rgba(10,10,10,.55) 0%,rgba(10,10,10,.1) 60%,rgba(10,10,10,0) 100%)}
.nav{position:absolute;top:62px;left:451px;display:flex;gap:0}
.nav a{font-size:13.5px;color:var(--white);text-decoration:none;margin-right:26px}
.nav a.is-active{color:var(--gold-text)}
.hero__title{position:absolute;left:142px;top:250px;font-family:var(--serif);font-size:41px;line-height:59px;text-transform:uppercase;color:var(--white)}
.hero__title em{font-style:normal;color:var(--gold-text)}
.hero__lead{position:absolute;left:145px;top:388px;font-size:15px;line-height:28px;color:var(--white)}
.scroll-line{position:absolute;left:599px;top:715px;width:1px;height:100px;background:#8a8a8a}
.scroll-dot{position:absolute;left:586px;top:826px;width:28px;height:28px;border:1px solid #8a8a8a;border-radius:50%}

/* Cards */
.card{position:absolute;top:1667px;width:272px}
.card__media{width:272px;height:348px}
.card__title{font-family:var(--serif);font-size:15.5px;text-transform:uppercase;margin-top:29px;letter-spacing:.3px;white-space:nowrap}
.card__text{font-size:12.5px;line-height:24px;color:var(--muted);margin-top:10px;width:270px}

/* Split */
.split{position:absolute;top:2302px;left:0;width:1200px;height:596px}
.split__left{position:absolute;left:0;top:0;width:600px;height:596px;background:linear-gradient(180deg,#0d0d0d,#161616)}
.split__right{position:absolute;left:600px;top:0;width:600px;height:596px;background:var(--gold);overflow:hidden}

/* Why */
.why-core{position:absolute;left:458px;top:3167px;width:284px;height:284px;border-radius:50%;background:var(--gold);box-shadow:0 0 0 11px #1f1a12}
.why-item{position:absolute;font-size:13.5px;font-weight:500;color:var(--white);white-space:nowrap}
.why-item--left{text-align:right}
.why-icon{position:absolute;width:46px;height:46px;border-radius:50%;background:#1d1d1d}
.why-icon svg{position:absolute;left:13px;top:13px}

/* Partners */
.partner{position:absolute;top:3805px;width:226px;height:96px;background:#111;display:flex;align-items:center;justify-content:center;gap:8px;font-size:16px;color:var(--white)}
.partner__dot{width:14px;height:14px;border-radius:50%;background:var(--white)}

/* Concierge */
.concierge{position:absolute;left:148px;top:4026px;width:904px;height:371px;background:var(--gold)}

/* Footer */
.footer-col{position:absolute;top:4474px}
.footer-col h4{font-family:var(--sans);font-weight:500;font-size:13px;color:var(--gold-text);margin-bottom:10px}
.footer-col a{display:block;font-size:11.5px;line-height:22px;color:var(--white);text-decoration:none}
.social{position:absolute;top:4574px;width:24px;height:24px;border-radius:50%;background:#1b1b1b}
.social::after{content:"";position:absolute;left:9px;top:9px;width:6px;height:6px;border-radius:1px;background:var(--white)}
</style>
</head>
<body>
<div class="page">

  <!-- Hero -->
  <header class="hero">
    <div class="hero__media" role="img" aria-label="Dark still life of cigars in a humidor, fragrance bottle, wristwatch, whisky glass, leather shoes and pen on black marble"></div>
    <div class="hero__shade"></div>

    <div class="brand" style="left:143px;top:22px;width:174px">
      <div class="brand__monogram"></div>
      <div class="brand__name">ORVANOGOODS</div>
      <div class="brand__sub">A division of KRWZ Hospitality</div>
      <div class="brand__tag">Purveyors of Luxury Lifestyle Accoutrements</div>
    </div>

    <nav class="nav">
      <a class="is-active" href="#">Home</a>
      <a href="#">About</a>
      <a href="#">Shop</a>
      <a href="#">Wholesale</a>
      <a href="#">Partners</a>
      <a href="#">Concierge</a>
    </nav>
    <a class="btn btn--gold" href="#" style="left:932px;top:50px;width:122px;height:42px">Contact Us</a>

    <h1 class="hero__title">Purveyors of luxury<br>lifestyle <em>accoutrements</em></h1>
    <p class="hero__lead">Curated collections for discerning individuals and<br>elevated hospitality environments.</p>
    <a class="btn btn--gold" href="#" style="left:145px;top:487px;width:203px;height:43px">Shop Retail Collections</a>
    <a class="btn btn--outline" href="#" style="left:356px;top:487px;width:246px;height:43px">Become a Wholesale Partner</a>

    <div class="scroll-line"></div>
  </header>
  <div class="scroll-dot">
    <svg width="28" height="28" viewBox="0 0 28 28" style="position:absolute;left:-1px;top:-1px"><path d="M9 12l5 5 5-5" fill="none" stroke="#bbb" stroke-width="1.4"/></svg>
  </div>

  <!-- Welcome -->
  <section>
    <span class="mark" style="top:940px"></span>
    <h2 class="title abs center" style="top:958px">Welcome To</h2>
    <p class="copy abs center" style="top:1043px;font-size:13px">Luxury is not excess.<br>It is intention, craftsmanship, and experience.</p>
    <p class="copy abs center" style="top:1118px;font-size:13px">At OrvanoGoods, we curate refined lifestyle goods for private clients and premium hospitality spaces. Every<br>product is selected to elevate atmosphere, identity, and indulgence — whether enjoyed personally or presented<br>to an audience that expects the exceptional.</p>
    <a class="btn btn--gold" href="#" style="left:529px;top:1236px;width:142px;height:41px">Explore More</a>
  </section>

  <!-- Featured collections -->
  <section>
    <span class="mark mark--left" style="left:144px;top:1464px"></span>
    <h2 class="title abs" style="left:143px;top:1487px">Featured <em>Collections</em></h2>
    <p class="copy abs" style="left:144px;top:1560px;font-size:13px">Explore a selection of elevated essentials and statement pieces designed to complement<br>refined lifestyles and sophisticated spaces.</p>
    <a class="btn btn--gold" href="#" style="left:851px;top:1567px;width:203px;height:43px">Explore the Collection</a>

    <article class="card" style="left:142px">
      <div class="card__media" role="img" aria-label="Close-up of a cigar with a banded wrapper in smoke" style="background:linear-gradient(160deg,#3a3430,#6b4426 45%,#1c1612)"></div>
      <h3 class="card__title">Cigar Accessories</h3>
      <p class="card__text">Precision-crafted tools and humidification essentials</p>
    </article>
    <article class="card" style="left:446px">
      <div class="card__media" role="img" aria-label="Grooming oil bottle and balm tins on a dark wooden board" style="background:radial-gradient(circle at 55% 45%,#6e5338,#3a2a1c 55%,#1a1410)"></div>
      <h3 class="card__title">Oils &amp; Grooming</h3>
      <p class="card__text">Elevated self-care for the modern gentleman</p>
    </article>
    <article class="card" style="left:750px">
      <div class="card__media" role="img" aria-label="Glass perfume bottle on black crushed stones" style="background:radial-gradient(circle at 50% 55%,#6a6660,#2a2826 45%,#121212)"></div>
      <h3 class="card__title">Fragrance</h3>
      <p class="card__text">Signature scents with depth and character</p>
    </article>
    <article class="card" style="left:1054px">
      <div class="card__media" role="img" aria-label="Leather handbag and folded knitwear in warm light" style="background:linear-gradient(180deg,#6b5535,#9a7a45 55%,#4e3a20)"></div>
      <h3 class="card__title">Attire &amp; Accessories</h3>
      <p class="card__text">Timeless pieces with confident presence</p>
    </article>
  </section>

  <!-- Private clients / trade partners -->
  <section class="split">
    <div class="split__left">
      <span class="mark mark--left" style="left:144px;top:152px"></span>
      <h2 class="title abs" style="left:143px;top:175px">For Private <em>Clients</em></h2>
      <p class="copy abs" style="left:144px;top:256px;font-size:13px;color:var(--white)">Indulgence curated for those who appreciate quality,<br>rarity, and detail. Shop refined lifestyle goods designed<br>for personal enjoyment and expression.</p>
      <a class="btn btn--gold" href="#" style="left:144px;top:368px;width:142px;height:42px">Shop Retail</a>
    </div>
    <div class="split__right">
      <svg class="abs" style="left:0;top:0" width="600" height="596" viewBox="0 0 600 596" aria-hidden="true">
        <g fill="none" stroke="#a88b5a" stroke-width="1" opacity=".6">
          <path d="M180 596c120-160 300-220 420-240"/>
          <path d="M210 596c120-150 290-205 390-222"/>
          <path d="M240 596c120-140 280-190 360-204"/>
          <path d="M270 596c110-130 260-175 330-186"/>
          <path d="M300 596c100-120 240-160 300-168"/>
        </g>
      </svg>
      <span class="mark mark--left" style="left:99px;top:152px"></span>
      <h2 class="title abs" style="left:99px;top:175px">For Trade Partners</h2>
      <p class="copy abs" style="left:99px;top:256px;font-size:13px;color:var(--white)">Elevate your lounge. Impress your clientele. Access exclusive<br>wholesale collections crafted to enhance premium<br>hospitality environments.</p>
      <a class="btn btn--dark" href="#" style="left:100px;top:368px;width:171px;height:42px">Wholesale Login</a>
    </div>
  </section>

  <!-- Why -->
  <section>
    <span class="mark" style="top:3038px"></span>
    <h2 class="title abs center" style="top:3061px">Why <em>OrvanoGoods</em></h2>

    <div class="why-core"></div>
    <div class="brand" style="left:458px;top:3255px;width:284px">
      <div class="brand__monogram"></div>
      <div class="brand__name" style="font-size:24px">ORVANOGOODS</div>
      <div class="brand__sub">A division of KRWZ Hospitality</div>
    </div>

    <span class="why-item why-item--left" style="right:793px;top:3163px">Craftsmanship Over Trends</span>
    <span class="why-item why-item--left" style="right:851px;top:3254px">Best Wholesale Partnerships</span>
    <span class="why-item why-item--left" style="right:851px;top:3345px">Concierge-Level Service</span>
    <span class="why-item why-item--left" style="right:793px;top:3435px">Designed to Elevate Experience</span>

    <span class="why-item" style="left:784px;top:3163px">Curated by hospitality professionals</span>
    <span class="why-item" style="left:846px;top:3254px">Luxury for Lifestyle &amp; Hospitality</span>
    <span class="why-item" style="left:846px;top:3345px">Rooted in Hospitality Expertise</span>
    <span class="why-item" style="left:784px;top:3435px">Exclusive &amp; Limited Access</span>

    <div class="why-icon" style="left:435px;top:3149px"><svg width="20" height="20" viewBox="0 0 20 20"><rect x="3" y="3" width="6" height="14" rx="2" fill="none" stroke="#9b7e4e" stroke-width="1.3"/><rect x="11" y="3" width="6" height="14" rx="2" fill="none" stroke="#9b7e4e" stroke-width="1.3"/></svg></div>
    <div class="why-icon" style="left:370px;top:3240px"><svg width="20" height="20" viewBox="0 0 20 20"><rect x="3" y="3" width="14" height="14" fill="none" stroke="#9b7e4e" stroke-width="1.3"/><path d="M3 10h14M10 3v14" stroke="#9b7e4e" stroke-width="1.3"/></svg></div>
    <div class="why-icon" style="left:370px;top:3331px"><svg width="20" height="20" viewBox="0 0 20 20"><circle cx="10" cy="7" r="3.5" fill="none" stroke="#9b7e4e" stroke-width="1.3"/><path d="M3 17c1-4 4-5 7-5s6 1 7 5" fill="none" stroke="#9b7e4e" stroke-width="1.3"/></svg></div>
    <div class="why-icon" style="left:433px;top:3421px"><svg width="20" height="20" viewBox="0 0 20 20"><circle cx="10" cy="10" r="7" fill="none" stroke="#9b7e4e" stroke-width="1.3"/><path d="M6 10l3 3 5-6" fill="none" stroke="#9b7e4e" stroke-width="1.3"/></svg></div>

    <div class="why-icon" style="left:721px;top:3149px"><svg width="20" height="20" viewBox="0 0 20 20"><rect x="4" y="8" width="12" height="9" fill="none" stroke="#9b7e4e" stroke-width="1.3"/><path d="M7 8V5h6v3" fill="none" stroke="#9b7e4e" stroke-width="1.3"/></svg></div>
    <div class="why-icon" style="left:783px;top:3240px"><svg width="20" height="20" viewBox="0 0 20 20"><path d="M10 2l2.4 5 5.6.8-4 3.9 1 5.5-5-2.7-5 2.7 1-5.5-4-3.9 5.6-.8z" fill="none" stroke="#9b7e4e" stroke-width="1.3"/></svg></div>
    <div class="why-icon" style="left:783px;top:3331px"><svg width="20" height="20" viewBox="0 0 20 20"><circle cx="10" cy="10" r="7" fill="none" stroke="#9b7e4e" stroke-width="1.3"/><circle cx="10" cy="10" r="2.5" fill="none" stroke="#9b7e4e" stroke-width="1.3"/></svg></div>
    <div class="why-icon" style="left:721px;top:3421px"><svg width="20" height="20" viewBox="0 0 20 20"><circle cx="10" cy="10" r="2" fill="none" stroke="#9b7e4e" stroke-width="1.3"/><circle cx="4" cy="4" r="1.6" fill="#9b7e4e"/><circle cx="16" cy="4" r="1.6" fill="#9b7e4e"/><circle cx="4" cy="16" r="1.6" fill="#9b7e4e"/><circle cx="16" cy="16" r="1.6" fill="#9b7e4e"/><path d="M5 5l3.5 3.5M15 5l-3.5 3.5M5 15l3.5-3.5M15 15l-3.5-3.5" stroke="#9b7e4e" stroke-width="1"/></svg></div>
  </section>

  <!-- Partners -->
  <section>
    <span class="mark" style="top:3650px"></span>
    <h2 class="title abs center" style="top:3672px">Our <em>Partners</em></h2>
    <p class="copy abs center" style="top:3740px;font-size:13.5px">Trusted by select lounges and hospitality partners who understand that atmosphere is everything.</p>
    <div class="partner" style="left:146px"><span class="partner__dot"></span>Velmont Lounge</div>
    <div class="partner" style="left:378px"><span class="partner__dot"></span>Ashgrove Club</div>
    <div class="partner" style="left:610px"><span class="partner__dot"></span>Caldera Room</div>
    <div class="partner" style="left:842px"><span class="partner__dot"></span>Noirwood House</div>
  </section>

  <!-- Concierge -->
  <section class="concierge">
    <span class="mark" style="top:78px"></span>
    <h2 class="title abs" style="left:0;width:904px;text-align:center;top:102px;font-size:35px">Concierge &amp; Custom Services</h2>
    <p class="copy abs" style="left:0;width:904px;text-align:center;top:170px;font-size:13.5px;color:var(--white)">From private orders to tailored wholesale solutions, our concierge team provides white-glove<br>support for clients and partners alike.</p>
    <a class="btn btn--dark" href="#" style="left:366px;top:254px;width:172px;height:40px">Contact us</a>
  </section>

  <!-- Footer -->
  <footer>
    <div class="brand" style="left:86px;top:4488px;width:176px">
      <div class="brand__monogram"></div>
      <div class="brand__name">ORVANOGOODS</div>
      <div class="brand__sub">A division of KRWZ Hospitality</div>
      <div class="brand__tag">Purveyors of Luxury Lifestyle Accoutrements</div>
    </div>
    <span class="social" style="left:120px"></span>
    <span class="social" style="left:156px"></span>
    <span class="social" style="left:192px"></span>

    <div class="footer-col" style="left:352px">
      <h4>Shop</h4>
      <a href="#">Shop All</a><a href="#">Cigar Accessories</a><a href="#">Oils &amp; Grooming</a><a href="#">Fragrance</a><a href="#">Attire</a><a href="#">Accessories</a><a href="#">Limited Editions</a>
    </div>
    <div class="footer-col" style="left:555px">
      <h4>Wholesale</h4>
      <a href="#">Wholesale Portal</a><a href="#">Partner Login</a><a href="#">Apply for Wholesale</a><a href="#">Why Partner With Us</a><a href="#">Corporate &amp; Event Gifting</a>
    </div>
    <div class="footer-col" style="left:776px">
      <h4>Company</h4>
      <a href="#">About Us</a><a href="#">Our Philosophy</a><a href="#">KRWZ Hospitality</a><a href="#">Partner Showcase</a>
    </div>
    <div class="footer-col" style="left:973px">
      <h4>Concierge &amp; Support</h4>
      <a href="#">Contact Concierge</a><a href="#">Custom Orders</a><a href="#">B2B Inquiries</a><a href="#">Shipping &amp; Returns</a><a href="#">FAQs</a>
    </div>

    <p class="abs center" style="top:4697px;font-size:11.5px;color:var(--white)">© 2026 OrvanoGoods. All Rights Reserved.</p>
  </footer>

</div>
</body>
</html>
```